Simple proffessional BC

I have a logo which I will attach below.
I would like the logo on the front of the card with these details in point form below:
Pre and Post Natal Yoga: Pregnancy Workshops: Hypnobirthing Courses
On the back of the card my details:
Marla Pennick
Facebook page- stretchbelliesbayridgefield
Mobile- 0491 352 718

I like the idea of the card being simple, possibly just the above on a plain coloured (eggshell?) card, a card that is textured.
I am open to suggestion if it appeals!
Thank you and good luck!

Target Market(s)

Pregnant women, 20's-40's

Requirements
Must have
• Simple, compliment logo.
Make logo the feature.
Should not have

• .

```html
<!DOCTYPE html>
<html lang="en">
<head>
<meta charset="utf-8">
<title>Stretch Bellies – Business Cards</title>
<link rel="stylesheet" href="https://fonts.googleapis.com/css2?family=Exo+2:wght@400;500;600&display=swap">
<style>
  :root {
    --backdrop: #9a9a9a;
    --card: #fbfbf9;
    --maroon: #8a2c2f;
    --maroon-soft: #a33a3c;
    --orange: #eda33b;
    --ink: #333333;
    --rule-dark: #3a3a3a;
  }
  * { box-sizing: border-box; margin: 0; padding: 0; }
  html, body {
    width: 1200px; height: 894px; overflow: hidden;
    background: var(--backdrop);
    font-family: "Exo 2", Arial, sans-serif;
  }
  .stage {
    width: 1200px; height: 894px;
    display: flex; align-items: center; justify-content: center; gap: 40px;
  }
  .card {
    position: relative;
    width: 540px; height: 309px;
    background: var(--card);
    overflow: hidden;
    box-shadow: 0 4px 14px rgba(0,0,0,0.18);
  }

  /* brand lockup */
  .brand-mark {
    position: absolute;
    width: 46px; height: 46px; border-radius: 50%;
    background: var(--orange);
  }
  .brand-name {
    position: absolute;
    font-weight: 400; color: var(--maroon);
    white-space: nowrap; letter-spacing: 0.5px;
  }

  /* contact card */
  .details .brand-mark { left: 18px; top: 20px; }
  .details .brand-name { left: 74px; top: 30px; font-size: 30px; }
  .details .header-rule {
    position: absolute; left: 0; top: 96px;
    width: 342px; height: 2px; background: var(--maroon);
  }
  .person { position: absolute; left: 350px; top: 104px; }
  .person-name {
    font-size: 14px; font-weight: 500; color: var(--maroon);
    letter-spacing: 0.6px; text-transform: uppercase;
  }
  .person-role { font-size: 12.5px; color: var(--maroon-soft); margin-top: 1px; }
  .services {
    position: absolute; left: 350px; top: 156px;
    list-style: none;
    font-size: 11.5px; line-height: 17px; color: var(--ink);
  }
  .contact-line {
    position: absolute; left: 22px; top: 222px;
    font-size: 12px; color: var(--ink); white-space: nowrap;
  }
  .contact-line .label {
    color: var(--maroon); font-weight: 600; font-size: 14px; margin-right: 3px;
  }
  .contact-line .item { margin-right: 10px; }
  .base-rule {
    position: absolute; left: 0; top: 254px;
    width: 100%; height: 2px; background: var(--rule-dark);
  }
  .base-band {
    position: absolute; left: 0; top: 262px;
    width: 100%; height: 47px; background: var(--maroon);
  }
  .band-stripes {
    position: absolute; left: 392px; top: 262px;
    display: flex; gap: 14px; height: 47px;
  }
  .band-stripes span { width: 8px; height: 100%; background: var(--card); }

  /* front card */
  .front .brand-mark { left: 300px; top: 82px; }
  .front .brand-name {
    left: 0; width: 100%; text-align: center;
    top: 130px; font-size: 32px;
  }
  .website {
    position: absolute; left: 0; width: 100%; top: 192px;
    text-align: center; font-size: 14px; font-weight: 600;
    color: var(--ink); letter-spacing: 0.8px;
  }
</style>
</head>
<body>
  <main class="stage">
    <section class="card details" aria-label="Contact side">
      <div class="brand-mark"></div>
      <div class="brand-name">Stretch Bellies</div>
      <div class="header-rule"></div>
      <div class="person">
        <p class="person-name">Marla Pennick</p>
        <p class="person-role">Managing Director</p>
      </div>
      <ul class="services">
        <li>Pre and Post Natal Yoga</li>
        <li>Pregnancy Workshops</li>
        <li>Hypnobirthing Courses</li>
      </ul>
      <p class="contact-line">
        <span class="item"><span class="label">P</span>0491 352 718</span>
        <span class="item"><span class="label">F</span>stretchbelliesbayridgefield</span>
        <span class="item"><span class="label">E</span>hello@stretchbellies.com</span>
      </p>
      <div class="base-rule"></div>
      <div class="base-band"></div>
      <div class="band-stripes">
        <span></span><span></span><span></span><span></span><span></span><span></span>
      </div>
    </section>

    <section class="card front" aria-label="Logo side">
      <div class="brand-mark"></div>
      <div class="brand-name">Stretch Bellies</div>
      <p class="website">www.stretchbellies.com</p>
    </section>
  </main>
</body>
</html>
```